Business Card Design

Electronic Security
Alarm Systems
CCTV
Electronic Access Control
Security System Integration

Industry/Entity Type

Business

Contact Information for Business Card

Gareth Linwood
PO Box 862
Ashgrove Qld 4071
Phone 07 38526147
Mob 0427395816

```html
<!DOCTYPE html>
<html lang="en">
<head>
<meta charset="utf-8">
<title>Business Card – Gareth Linwood</title>
<link rel="stylesheet" href="https://fonts.googleapis.com/css2?family=Arimo:wght@400;700&display=swap">
<style>
  :root {
    --backdrop: #4a4550;
    --card: #ffffff;
    --ink: #111111;
    --band: #000000;
    --band-text: #ffffff;
    --brand: #2a8fcf;
    --accent: #f39a1e;
  }
  html, body {
    margin: 0;
    padding: 0;
    width: 1200px;
    height: 960px;
    overflow: hidden;
    background: var(--backdrop);
    font-family: "Arimo", Arial, sans-serif;
  }
  .card {
    position: absolute;
    left: 150px;
    top: 223px;
    width: 900px;
    height: 514px;
    background: var(--card);
    box-shadow: 0 10px 30px rgba(0,0,0,0.35);
    overflow: hidden;
  }
  .holder-name {
    position: absolute;
    left: 110px;
    top: 180px;
    margin: 0;
    font-size: 27px;
    font-weight: 700;
    letter-spacing: 0.5px;
    color: var(--ink);
    text-transform: uppercase;
  }
  .contact-list {
    position: absolute;
    left: 210px;
    top: 268px;
    margin: 0;
    padding: 0;
    list-style: none;
    font-size: 19px;
    color: var(--ink);
  }
  .contact-list li {
    display: flex;
    align-items: center;
    gap: 14px;
    height: 30px;
  }
  .contact-icon {
    width: 20px;
    height: 20px;
    flex: none;
  }
  .brand {
    position: absolute;
    right: 90px;
    top: 200px;
    display: flex;
    align-items: center;
    gap: 16px;
  }
  .brand-mark {
    width: 22px;
    height: 22px;
    background: var(--accent);
  }
  .brand-name {
    font-size: 62px;
    font-weight: 400;
    letter-spacing: 2px;
    color: var(--brand);
  }
  .band-rule {
    position: absolute;
    left: 0;
    right: 0;
    top: 392px;
    height: 3px;
    background: var(--band);
  }
  .service-band {
    position: absolute;
    left: 0;
    right: 0;
    top: 401px;
    bottom: 0;
    background: var(--band);
    color: var(--band-text);
    font-size: 20px;
    line-height: 28px;
    padding: 28px 0 0 340px;
    box-sizing: border-box;
  }
  .service-band p { margin: 0; }
</style>
</head>
<body>
  <article class="card">
    <h1 class="holder-name">Gareth Linwood</h1>

    <ul class="contact-list">
      <li>
        <svg class="contact-icon" viewBox="0 0 20 20" aria-hidden="true">
          <rect width="20" height="20" fill="#111"/>
          <rect x="6" y="3.5" width="8" height="13" rx="1.5" fill="none" stroke="#f39a1e" stroke-width="1.8"/>
        </svg>
        <span>0427395816</span>
      </li>
      <li>
        <svg class="contact-icon" viewBox="0 0 20 20" aria-hidden="true">
          <rect width="20" height="20" fill="#111"/>
          <path d="M5 6c0 5 4 9 9 9l1.5-2-3-1.5-1.2 1.2c-1.6-.8-2.7-1.9-3.5-3.5L9 8 7.5 5 5 6z" fill="#f39a1e"/>
        </svg>
        <span>07 38526147</span>
      </li>
      <li>
        <svg class="contact-icon" viewBox="0 0 20 20" aria-hidden="true">
          <rect width="20" height="20" fill="#111"/>
          <path d="M10 3.5a4.5 4.5 0 0 0-4.5 4.5c0 3.3 4.5 8.5 4.5 8.5s4.5-5.2 4.5-8.5A4.5 4.5 0 0 0 10 3.5z" fill="#f39a1e"/>
          <circle cx="10" cy="8" r="1.7" fill="#111"/>
        </svg>
        <span>PO Box 862 Ashgrove Qld 4071</span>
      </li>
    </ul>

    <div class="brand">
      <span class="brand-mark"></span>
      <span class="brand-name">HALDEN</span>
    </div>

    <div class="band-rule"></div>
    <section class="service-band">
      <p>Electronic Security, Alarm Systems, CCTV</p>
      <p>Electronic Access Control, Security System Integration</p>
    </section>
  </article>
</body>
</html>
```